Satchel & Sundial needs new business card design

I need a new business card design. I'm looking for out-of-the-box design which represents the freedom of being a location independent entrepreneur.
I offer coaching, retreats and trips.
I would like to see designs with and without the photo.
Colors I use are black (#000000), green (#25A796) and brown (#D7C38C)
Website satchelandsundial.example

Target Market(s)

location independent entrepreneurs, digital nomads, people looking to swap the 9 to 5 for a lifestyle business

Industry/Entity Type

Business

Contact Information for Business Card

Dorota Falkner
Your Lifestyle Business Coach, Retreat & Trip Leader
http://satchelandsundial.example
hello@satchelandsundial.example
Live a life you don't need a holiday from

Font styles to use
Serif
Sans Serif

Requirements
Must have
• One side should contain only the logo. I would also consider having the "Live a life you don't need a holiday from" on that side too (depending on how it looks)
• Please show both sides on the designs.

```html
<!DOCTYPE html>
<html lang="en">
<head>
<meta charset="utf-8">
<title>Satchel &amp; Sundial — Business Card</title>
<link rel="stylesheet" href="https://fonts.googleapis.com/css2?family=Source+Sans+3:wght@400;600;700&family=Amatic+SC:wght@700&display=swap">
<style>
  :root {
    --ink: #231f20;
    --teal: #25a796;
    --teal-card: #24a898;
    --white: #ffffff;
    --muted: #b9b9b9;
    --bg-top: #c8c8c8;
    --bg-bottom: #fbfbfb;
  }
  * { margin: 0; padding: 0; box-sizing: border-box; }
  html, body { width: 1200px; height: 900px; overflow: hidden; }
  body {
    position: relative;
    background: linear-gradient(to bottom, var(--bg-top), var(--bg-bottom));
    font-family: "Source Sans 3", sans-serif;
  }
  .card-shapes { position: absolute; left: 0; top: 0; }
  .front, .back {
    position: absolute; left: 0; top: 0;
    width: 1200px; height: 900px;
    white-space: nowrap;
  }

  .holder-name {
    position: absolute; left: 183px; top: 340px;
    font-size: 16px; font-weight: 700; line-height: 20px; color: var(--teal);
  }
  .holder-role {
    position: absolute; left: 183px; top: 361px;
    font-size: 12.5px; line-height: 16px; color: var(--muted);
  }
  .front-wordmark {
    position: absolute; left: 330px; top: 404px; width: 222px;
    text-align: right;
    font-size: 25px; font-weight: 600; line-height: 1; color: var(--white);
  }
  .contact-list {
    position: absolute; left: 182px; top: 462px; list-style: none;
    font-size: 12.5px; line-height: 17px; color: var(--muted);
  }
  .contact-list li { display: flex; align-items: center; gap: 6px; }
  .contact-list svg { width: 8px; height: 8px; flex: none; }
  .tagline {
    position: absolute; left: 178px; top: 514px;
    font-family: "Amatic SC", sans-serif; font-weight: 700;
    font-size: 18px; line-height: 22px; letter-spacing: 1.6px; color: var(--teal);
  }
  .back-wordmark {
    position: absolute; left: 640px; top: 420px; width: 380px;
    text-align: center;
    font-size: 36px; font-weight: 600; line-height: 1; color: var(--white);
  }
</style>
</head>
<body>
  <svg class="card-shapes" width="1200" height="900" viewBox="0 0 1200 900" aria-hidden="true">
    <path fill="var(--ink)" d="M156,306 H515 C560,306 585,380 585,441 C585,502 560,577 520,577 H156 Q148,577 148,569 V314 Q148,306 156,306 Z"/>
    <path fill="var(--teal)" d="M156,306 H160 V577 H156 Q148,577 148,569 V314 Q148,306 156,306 Z"/>
    <path fill="var(--teal-card)" d="M1038,306 H670 C625,306 608,380 608,441 C608,502 625,577 672,577 H1038 Q1046,577 1046,569 V314 Q1046,306 1038,306 Z"/>
    <path fill="var(--ink)" d="M1034,306 H1038 Q1046,306 1046,314 V569 Q1046,577 1038,577 H1034 Z"/>
  </svg>

  <section class="front" aria-label="Card front">
    <h1 class="holder-name">Dorota Falkner</h1>
    <p class="holder-role">Your Lifestyle Business Coach,<br>Retreat &amp; Trip Leader</p>
    <p class="front-wordmark">Satchel &amp; Sundial</p>
    <ul class="contact-list">
      <li>
        <svg viewBox="0 0 8 8"><rect x="0" y="1" width="8" height="6" fill="var(--teal)"/><path d="M0,1 L4,4.5 L8,1" fill="none" stroke="var(--ink)" stroke-width="0.9"/></svg>
        hello@satchelandsundial.example
      </li>
      <li>
        <svg viewBox="0 0 8 8"><circle cx="4" cy="4" r="4" fill="var(--teal)"/></svg>
        www.satchelandsundial.example
      </li>
    </ul>
    <p class="tagline">LIVE A LIFE YOU DON'T NEED A HOLIDAY FROM</p>
  </section>

  <section class="back" aria-label="Card back">
    <p class="back-wordmark">Satchel &amp; Sundial</p>
  </section>
</body>
</html>
```